Packaging for a luxury Hair Straightener
very good and professional design and was very responding to all my request.
Zielgruppe
We are an Israeli company, that provides high end hair tools (straightener etc.) and hair care (Shampoo etc.). Our target market are women in the age between 20-50 years, that pay extra for higher quality. Our items are rated as high end luxury products. Our main target market is in Israel.
Aufgabenstellung
We are currently looking for a new design for our hair straightener package. We recently worked on our logo and now want to restyle the current packaging with the new logo. The package needs to be simple modern and luxurious, but not as simple as it is now. It needs to have a more professional look with different fonts etc.
Also the current design from where everything is needs to be changed. Like for example what is written on the sides of the box or inside the box to have a catchy phrase instead of the logo. The straightener is also white and has the rose gold logo on it. The slogan of the company is 'give your hair what it deserves'.
The pictures of the current design will be attached. It will be printed on both sides and rose gold hot stamping printing should be in the design but other colors are welcome as well. The box is magnetic box.

```html
<!DOCTYPE html>
<html lang="en">
<head>
<meta charset="utf-8">
<title>Noravel Atelier – Hair Straightener Box</title>
<link rel="stylesheet" href="https://fonts.googleapis.com/css2?family=Raleway:wght@300;400&family=Sacramento&family=Roboto:wght@300&display=swap">
<style>
  :root {
    --rose: #c9967f;
    --rose-soft: #d9ad98;
    --paper: #fbfbfb;
    --paper-shade: #f1f1f1;
    --backdrop: #d3d3d3;
  }
  * { margin: 0; padding: 0; box-sizing: border-box; }
  html, body { width: 1200px; height: 1183px; overflow: hidden; background: var(--backdrop); }
  .canvas { position: relative; width: 1200px; height: 1183px; }

  .lid-top {
    position: absolute; left: 100px; top: 170px; width: 1000px; height: 520px;
    background: var(--paper); box-shadow: 0 6px 24px rgba(0,0,0,.08);
    overflow: hidden;
  }
  .quality-seal { position: absolute; left: 60px; top: 40px; }
  .hero-name {
    position: absolute; left: 56px; top: 190px;
    font-family: "Raleway", sans-serif; font-weight: 300;
    font-size: 170px; line-height: 1; letter-spacing: 4px; color: var(--rose);
    white-space: nowrap;
  }

  .brand-mark {
    display: flex; align-items: center; gap: 10px;
    font-family: "Raleway", sans-serif; font-weight: 300;
    font-size: 26px; letter-spacing: 4px; color: var(--rose);
    text-transform: uppercase; white-space: nowrap;
  }
  .brand-mark .square { width: 14px; height: 14px; border: 1.5px solid var(--rose); flex: none; }
  .lid-top .brand-mark { position: absolute; right: 60px; top: 40px; }

  .product-line { position: absolute; right: 60px; top: 100px; text-align: right; color: var(--rose); font-family: "Raleway", sans-serif; }
  .product-line .category { font-weight: 300; font-size: 34px; letter-spacing: 2px; line-height: 1; }
  .product-line .category-sub { font-weight: 400; font-size: 11px; letter-spacing: 2px; margin: 4px 0 8px; }
  .product-line .model {
    display: inline-block; background: var(--rose); color: var(--paper);
    font-weight: 300; font-size: 40px; line-height: 1.2; padding: 4px 26px; border-radius: 3px; letter-spacing: 2px;
  }

  .slogan {
    position: absolute; right: 60px; bottom: 40px;
    font-family: "Sacramento", cursive; font-size: 44px; color: var(--rose); white-space: nowrap;
  }

  .box-end {
    position: absolute; left: 100px; top: 720px; width: 300px; height: 170px;
    background: var(--paper-shade); padding: 26px 24px;
    font-family: "Roboto", sans-serif; font-weight: 300; font-size: 14px; line-height: 1.45;
    color: var(--rose); text-align: center;
  }
  .box-front {
    position: absolute; left: 420px; top: 720px; width: 680px; height: 170px;
    background: var(--paper-shade);
    display: flex; align-items: center; justify-content: center;
  }
</style>
</head>
<body>
<main class="canvas">
  <section class="lid-top">
    <svg class="quality-seal" width="120" height="120" viewBox="0 0 150 150" role="img" aria-label="Titanium quality seal">
      <circle cx="75" cy="75" r="70" fill="var(--rose)"/>
      <circle cx="75" cy="75" r="54" fill="none" stroke="var(--paper)" stroke-width="2"/>
    </svg>
    <div class="hero-name">Noravel</div>

    <div class="brand-mark"><span class="square"></span>Noravel Atelier</div>

    <div class="product-line">
      <div class="category">HAIR</div>
      <div class="category-sub">STRAIGHTENER</div>
      <div class="model">R7</div>
    </div>

    <p class="slogan">Give your hair what it deserves</p>
  </section>

  <section class="box-end">
    <p>“Lorem ipsum dolor sit amet, consectetur adipiscing elit, sed do eiusmod tempor incididunt ut labore et dolore magna aliqua. Ut enim ad minim veniam, quis nostrud exercitation”</p>
  </section>

  <section class="box-front">
    <div class="brand-mark"><span class="square"></span>Noravel Atelier</div>
  </section>
</main>
</body>
</html>
```